Maple Tide Photography business card design required

Needing business card made up for my new photography business.

Target Market(s)

Target will mostly be regular people with the occasional industrial or commercial customer.

Industry/Entity Type

Business

Font styles to use
Sans Serif

Colors

Designer to choose colors to be used in the design.

Requirements
Must have
• Lionel Baxwick
Ph: 0471 526 083
Email: info@mapletidephotography.com
Web: www.mapletidephotography.com

On the back possibly links for social media including Facebook, Flickr and Instagram (links to be determined).

```html
<!DOCTYPE html>
<html lang="en">
<head>
<meta charset="utf-8">
<title>Maple Tide Photography – Business Card</title>
<link href="https://fonts.googleapis.com/css2?family=Lato:wght@700;900&family=Questrial&display=swap" rel="stylesheet">
<style>
  :root {
    --backdrop: #2b2b2b;
    --card: #f4f4f4;
    --accent: #1c8ccc;
    --ink: #2e2e2e;
    --muted: #6d6d6d;
    --plate: #0d0d0d;
    --social: #b9bcc2;
  }
  * { box-sizing: border-box; margin: 0; padding: 0; }
  html, body { width: 1200px; height: 997px; overflow: hidden; }
  body { background: var(--backdrop); position: relative; font-family: "Questrial", sans-serif; }

  .card {
    position: absolute; left: 240px; width: 720px; height: 410px;
    background: var(--card); overflow: hidden;
    box-shadow: 0 10px 30px rgba(0,0,0,.45);
  }
  .card::after {
    content: ""; position: absolute; left: 0; right: 0; bottom: 0; height: 16px; background: var(--accent);
  }
  .card--back { top: 60px; }
  .card--front { top: 527px; }

  /* corner frame brackets */
  .bracket { position: absolute; width: 100px; height: 70px; border-color: var(--muted); border-style: solid; border-width: 0; }
  .bracket--top-right { top: 36px; right: 40px; border-top-width: 1.5px; border-right-width: 1.5px; }
  .bracket--bottom-left { bottom: 50px; left: 40px; border-bottom-width: 1.5px; border-left-width: 1.5px; }

  /* brand name set as plain text */
  .brand { position: absolute; font-family: "Lato", sans-serif; font-weight: 900; color: var(--ink); text-transform: uppercase; line-height: 1; letter-spacing: 1px; white-space: nowrap; }
  .card--back .brand { left: 50%; top: 50%; transform: translate(-50%, -50%); font-size: 44px; }
  .card--front .brand { left: 60px; top: 102px; font-size: 34px; }

  /* name plate: plain dark band */
  .plate { position: absolute; right: 0; top: 34px; width: 330px; height: 128px; background: var(--plate);
    display: flex; flex-direction: column; align-items: center; justify-content: center;
    font-family: "Lato", sans-serif; font-weight: 700; color: #fff; text-transform: uppercase; }
  .plate__name { font-size: 22px; letter-spacing: .5px; }
  .plate__role { font-size: 15px; letter-spacing: 1px; margin-top: 4px; }

  /* contacts */
  .contacts { position: absolute; left: 390px; top: 210px; list-style: none; color: var(--ink); font-size: 18px; }
  .contacts li { display: flex; align-items: center; gap: 12px; height: 32px; white-space: nowrap; }
  .contacts svg { width: 20px; height: 20px; flex: none; }

  /* social placeholders */
  .social { position: absolute; left: 50px; bottom: 52px; display: flex; gap: 14px; }
  .social span { width: 42px; height: 42px; border-radius: 50%; background: var(--social); box-shadow: 0 2px 4px rgba(0,0,0,.25); }
</style>
</head>
<body>

<section class="card card--back" aria-label="Card back">
  <div class="bracket bracket--top-right"></div>
  <div class="bracket bracket--bottom-left"></div>
  <div class="brand">Maple Tide</div>
</section>

<section class="card card--front" aria-label="Card front">
  <div class="brand">Maple Tide</div>

  <div class="plate">
    <span class="plate__name">Lionel Baxwick</span>
    <span class="plate__role">Photographer</span>
  </div>

  <ul class="contacts">
    <li>
      <svg viewBox="0 0 20 20" aria-hidden="true"><path d="M3 8c0-3 3-4 7-4s7 1 7 4l-3 1-1-2H7L6 9 3 8zM5 10h10l1 6H4l1-6z" fill="var(--accent)"/></svg>
      <span>0471 526 083</span>
    </li>
    <li>
      <svg viewBox="0 0 20 20" aria-hidden="true"><rect x="2" y="5" width="16" height="11" fill="var(--accent)"/><path d="M2 5l8 6 8-6" fill="none" stroke="#fff" stroke-width="1.5"/></svg>
      <span>info@mapletidephotography.com</span>
    </li>
    <li>
      <svg viewBox="0 0 20 20" aria-hidden="true"><g fill="none" stroke="var(--accent)" stroke-width="2.2" stroke-linecap="round"><path d="M8 12l4-4"/><path d="M9 6l2-2a3 3 0 014 4l-2 2"/><path d="M11 14l-2 2a3 3 0 01-4-4l2-2"/></g></svg>
      <span>www.mapletidephotography.com</span>
    </li>
  </ul>

  <div class="social" aria-label="Social media links">
    <span></span><span></span><span></span>
  </div>
</section>

</body>
</html>
```